​Silver Harbor Rhythm provides personal, friendly service in a fun and high energy environment. We are based in Vermont.

We would like a card that appeals to a wide range of audiences as we do a wide range of events. Please feel free to check out our website silverharborrhythm.net for inspiration.

Target Market(s)

weddings, corporate, birthday parties, colleges

Industry/Entity Type

Business

Contact Information for Business Card

Silver Harbor Rhythm
Providing Entertainment For All Occasions
555 274 9160
silverharborrhythm@mailnest.net
silverharborrhythm.net

```html
<!DOCTYPE html>
<html lang="en">
<head>
<meta charset="utf-8">
<title>Silver Harbor Rhythm – Business Card</title>
<link rel="stylesheet" href="https://fonts.googleapis.com/css2?family=Open+Sans:wght@400;600;700;800&display=swap">
<style>
  :root {
    --green: #2f5d1e;
    --green-dark: #1e4210;
    --green-light: #4f7f35;
    --ink: #3d3d3d;
    --ink-soft: #5a5a5a;
    --paper: #ffffff;
    --backdrop: #e9e6e1;
  }
  * { box-sizing: border-box; margin: 0; padding: 0; }
  html, body { width: 1200px; height: 1200px; overflow: hidden; }
  body {
    background: var(--backdrop);
    font-family: "Open Sans", Arial, sans-serif;
    position: relative;
  }
  .card {
    position: absolute;
    width: 760px;
    height: 440px;
    background: var(--paper);
    border-radius: 34px;
    overflow: hidden;
    box-shadow: 0 6px 18px rgba(0,0,0,0.18);
  }
  .card--front { left: 80px; top: 110px; }
  .card--back { left: 360px; top: 650px; }

  /* brand name block */
  .brand {
    position: absolute;
    display: flex;
    align-items: center;
    gap: 14px;
    color: var(--green);
    font-weight: 800;
    letter-spacing: -0.5px;
    white-space: nowrap;
    z-index: 2;
  }
  .brand__square { background: var(--green); flex: none; }
  .card--front .brand { left: 66px; top: 96px; font-size: 36px; }
  .card--front .brand__square { width: 26px; height: 26px; }
  .card--back .brand {
    left: 0; right: 0; top: 150px;
    justify-content: center;
    font-size: 48px;
  }
  .card--back .brand__square { width: 34px; height: 34px; }

  /* contact list */
  .contact {
    position: absolute;
    left: 72px;
    top: 196px;
    list-style: none;
    font-size: 17px;
    color: var(--ink);
    line-height: 30px;
    z-index: 2;
  }
  .contact__item { display: flex; align-items: center; gap: 10px; }
  .contact__icon { width: 16px; height: 16px; flex: none; }

  .address {
    position: absolute;
    left: 72px;
    top: 304px;
    font-size: 16px;
    color: var(--ink);
    z-index: 2;
  }

  .wave { position: absolute; left: 0; top: 0; width: 760px; height: 440px; z-index: 1; }

  .signature {
    position: absolute;
    right: 40px;
    top: 358px;
    text-align: right;
    color: var(--paper);
    z-index: 2;
  }
  .signature__name { font-size: 24px; font-weight: 700; line-height: 30px; }
  .signature__title { font-size: 17px; font-weight: 400; line-height: 26px; }

  .website {
    position: absolute;
    left: 0; right: 0;
    top: 262px;
    text-align: center;
    font-size: 26px;
    font-weight: 600;
    letter-spacing: 1.5px;
    color: var(--ink-soft);
  }
</style>
</head>
<body>

  <section class="card card--front" aria-label="Business card front">
    <svg class="wave" viewBox="0 0 760 440" aria-hidden="true">
      <path d="M0,352 C150,360 260,415 400,412 C500,409 560,290 760,250 L760,440 L0,440 Z" fill="var(--green)"/>
      <path d="M0,398 C170,408 280,448 420,448 C540,448 640,365 760,328 L760,440 L0,440 Z" fill="var(--green-dark)"/>
      <path d="M0,370 C150,378 260,432 400,430 C500,427 560,308 760,268" fill="none" stroke="var(--paper)" stroke-width="6"/>
      <path d="M0,386 C160,394 270,442 410,442 C540,442 620,345 760,306" fill="none" stroke="var(--green-light)" stroke-width="3"/>
    </svg>

    <div class="brand">
      <span class="brand__square"></span>
      <span class="brand__name">Silver Harbor Rhythm</span>
    </div>

    <ul class="contact">
      <li class="contact__item">
        <svg class="contact__icon" viewBox="0 0 16 16" aria-hidden="true">
          <circle cx="8" cy="8" r="8" fill="var(--green)"/>
          <path d="M5.2,4.2 L6.6,4 L7.3,6 L6.4,6.8 C6.9,7.9 7.9,8.9 9,9.5 L9.9,8.6 L11.9,9.3 L11.7,10.8 C8.3,11.2 4.8,7.7 5.2,4.2 Z" fill="var(--paper)"/>
        </svg>
        <span>555 274 9160</span>
      </li>
      <li class="contact__item">
        <svg class="contact__icon" viewBox="0 0 16 16" aria-hidden="true">
          <circle cx="8" cy="8" r="8" fill="var(--green)"/>
          <rect x="4" y="5" width="8" height="6" fill="var(--paper)"/>
          <path d="M4,5 L8,8.3 L12,5" fill="none" stroke="var(--green)" stroke-width="1"/>
        </svg>
        <span>silverharborrhythm@mailnest.net</span>
      </li>
      <li class="contact__item">
        <svg class="contact__icon" viewBox="0 0 16 16" aria-hidden="true">
          <circle cx="8" cy="8" r="8" fill="var(--green)"/>
          <circle cx="8" cy="8" r="4.2" fill="none" stroke="var(--paper)" stroke-width="1.2"/>
          <path d="M3.8,8 H12.2 M8,3.8 V12.2" stroke="var(--paper)" stroke-width="1"/>
        </svg>
        <span>silverharborrhythm.net</span>
      </li>
    </ul>

    <p class="address">Sreet Name, City Name, Zip Code-00000</p>

    <div class="signature">
      <p class="signature__name">Your Name</p>
      <p class="signature__title">Title</p>
    </div>
  </section>

  <section class="card card--back" aria-label="Business card back">
    <div class="brand">
      <span class="brand__square"></span>
      <span class="brand__name">Silver Harbor Rhythm</span>
    </div>
    <p class="website">www.silverharborrhythm.net</p>
  </section>

</body>
</html>
```